Need help in designing new business card utilizing our new logo.

BuildMark Solutions works with Construction Business Owners, Managers & IT Professionals to strengthen software usage and increase user productivity.

Our Construction Accounting and Mobile Field Management Software Clients engage with us in the following areas:

New Software Implementations
Software Re-Implementations
Redesigning Software Usage at the User Level
Project Coordination & Management
Continued Software Support

Old tag line:
Weighing Options - Implementing Solutions

www.buildmark-solutions.example

Ridge 4 is a product, but not needed for a new business card.

```html
<!DOCTYPE html>
<html lang="en">
<head>
<meta charset="utf-8">
<title>BuildMark Solutions – Business Card</title>
<link href="https://fonts.googleapis.com/css2?family=Roboto:wght@400;500;700&display=swap" rel="stylesheet">
<style>
  :root {
    --backdrop: #3b3b3d;
    --card: #2a2b2e;
    --brand-blue: #0c4797;
    --light-grey: #c4c5c7;
    --mid-grey: #8c8d90;
    --white: #ffffff;
  }
  * { margin: 0; padding: 0; box-sizing: border-box; }
  html, body {
    width: 799px; height: 1200px; overflow: hidden;
    background: var(--backdrop);
    font-family: "Roboto", Arial, sans-serif;
  }
  .card {
    position: absolute; left: 90px;
    width: 620px; height: 354px;
    background: var(--card);
    border-radius: 22px;
    overflow: hidden;
    box-shadow: 0 12px 30px rgba(0,0,0,.45);
  }
  .card--front { top: 150px; }
  .card--back { top: 700px; }

  /* Front */
  .front-brand {
    position: absolute; top: 52px; left: 0; right: 0;
    display: flex; align-items: center; justify-content: center; gap: 18px;
  }
  .brand-square { width: 48px; height: 48px; background: var(--mid-grey); }
  .front-brand .brand-name {
    font-size: 38px; font-weight: 500; color: var(--mid-grey);
  }
  .service-band {
    position: absolute; top: 140px; left: 0; right: 0; height: 110px;
    background: var(--brand-blue);
    display: flex; flex-direction: column; justify-content: center; align-items: center;
    color: var(--white); font-size: 17px; line-height: 1.45; text-align: center;
  }
  .front-web {
    position: absolute; top: 282px; left: 0; right: 0;
    display: flex; align-items: center; justify-content: center; gap: 20px;
    color: var(--white); font-size: 16px;
  }
  .front-web .rule { width: 44px; height: 2px; background: var(--light-grey); }

  /* Back */
  .back-brand {
    position: absolute; top: 26px; left: 34px;
    font-size: 30px; font-weight: 700; color: var(--brand-blue);
  }
  .person { position: absolute; top: 80px; left: 34px; }
  .person-name { font-size: 24px; font-weight: 700; color: var(--white); }
  .person-role { font-size: 13px; color: var(--light-grey); margin-top: 2px; }
  .contact-list {
    position: absolute; top: 140px; left: 34px;
    list-style: none; color: var(--white); font-size: 13.5px; line-height: 1.6;
  }
  .contact-list li { display: flex; align-items: center; gap: 9px; }
  .contact-list svg { width: 13px; height: 13px; fill: var(--light-grey); flex: none; }
  .address {
    position: absolute; top: 245px; left: 34px;
    color: var(--white); font-size: 13.5px; line-height: 1.45;
  }
  .mark-block {
    position: absolute; top: 70px; right: 40px;
    width: 200px; height: 200px; background: var(--brand-blue);
  }
  .grey-strip {
    position: absolute; left: 0; bottom: 0; width: 260px; height: 22px;
    background: var(--light-grey);
  }
  .tagline-strip {
    position: absolute; right: 0; bottom: 0; width: 380px; height: 40px;
    background: var(--brand-blue); border-top-left-radius: 18px;
    display: flex; align-items: center; justify-content: center;
    color: var(--white); font-size: 16px;
  }
</style>
</head>
<body>

<section class="card card--front">
  <div class="front-brand">
    <span class="brand-square"></span>
    <span class="brand-name">BuildMark Solutions</span>
  </div>
  <div class="service-band">
    <p>New Software Implementations &nbsp;|&nbsp; Software Re-Implementations</p>
    <p>Redesigning Software Usage at the User Level</p>
    <p>Project Coordination &amp; Management &nbsp;|&nbsp; Continued Software Support</p>
  </div>
  <div class="front-web">
    <span class="rule"></span>
    <span>www.buildmark-solutions.example</span>
    <span class="rule"></span>
  </div>
</section>

<section class="card card--back">
  <div class="back-brand">BuildMark Solutions</div>
  <div class="person">
    <p class="person-name">Dana R. Whitfield</p>
    <p class="person-role">Owner</p>
  </div>
  <ul class="contact-list">
    <li><svg viewBox="0 0 24 24"><path d="M6.6 10.8a15 15 0 0 0 6.6 6.6l2.2-2.2c.3-.3.7-.4 1-.2 1.1.4 2.3.6 3.6.6.6 0 1 .4 1 1V20c0 .6-.4 1-1 1A17 17 0 0 1 3 4c0-.6.4-1 1-1h3.5c.6 0 1 .4 1 1 0 1.3.2 2.5.6 3.6.1.3 0 .7-.2 1z"/></svg>555-014-7567</li>
    <li><svg viewBox="0 0 24 24"><path d="M6.6 10.8a15 15 0 0 0 6.6 6.6l2.2-2.2c.3-.3.7-.4 1-.2 1.1.4 2.3.6 3.6.6.6 0 1 .4 1 1V20c0 .6-.4 1-1 1A17 17 0 0 1 3 4c0-.6.4-1 1-1h3.5c.6 0 1 .4 1 1 0 1.3.2 2.5.6 3.6.1.3 0 .7-.2 1z"/></svg>555-019-6650 ext. 100</li>
    <li><svg viewBox="0 0 24 24"><path d="M2 5h20v14H2zm2 2v.5l8 5 8-5V7l-8 5z"/></svg>dana.whitfield@buildmark-solutions.example</li>
    <li><svg viewBox="0 0 24 24"><path d="M12 2a10 10 0 1 0 0 20 10 10 0 0 0 0-20zm0 2c1 1.3 1.8 3 2.1 5H9.9C10.2 7 11 5.3 12 4zM4.3 11h3.6a16 16 0 0 0 0 2H4.3a8 8 0 0 1 0-2zm5.6 0h4.2a14 14 0 0 1 0 2H9.9a14 14 0 0 1 0-2zm6.2 0h3.6a8 8 0 0 1 0 2h-3.6a16 16 0 0 0 0-2zM9.9 15h4.2c-.3 2-1.1 3.7-2.1 5-1-1.3-1.8-3-2.1-5z"/></svg>www.buildmark-solutions.example</li>
  </ul>
  <div class="address">
    <p>48B Harbor Lane - Suite 210</p>
    <p>Millbrook Falls, NY 10000</p>
  </div>
  <div class="mark-block"></div>
  <div class="grey-strip"></div>
  <div class="tagline-strip">Weighing Options - Implementing Solutions</div>
</section>

</body>
</html>
```